Business Performance Improvement Book Cover Design Project

We need a book cover design for a new company, based in Eastern Australia, called Brovanta Consulting. We advise clients on process improvement, continuous improvement and business performance improvement, especially in the manufacturing areas and Fast Moving Consumer Goods industries.
We have a written a book designed to demonstrate our very high calibre of knowledge and to use as a marketing tool for prospective clients. We hope to give it out at training seminars and as a comprehensive business card.

Title of the book is: A rounded method for Enterprise Results Advancement.
Subtitle: Shape a Steady Refinement method to fit your firm's character.
Author: by Gareth Polwyn
Back Cover: No need for a bar code in this edition. An important aspect is that we will distribute by hand. Text below for back page.

'For the experienced Business Performers, this book is designed to offer an insight into the advantages and an example of an approach to Business Improvement. It is not the only way but it is tried and tested in world class companies and it works. For those new to Continuous Improvement, it offers a helpful introduction to a holistic business improvement system, an overview of important success factors and pitfalls, recommendations on how to implement tools and methods and a quick guide to see when to use which tools. '

'Consultancies are one of many tools management teams can engage and management must make sure the consultants tailor their approach to suit its business needs and culture and not vice versa.'

End of text for back cover.

Business Performance Improvement is also known as or can include:
Continuous Improvement
Process Improvement
Lean Six Sigma
Operational Excellence
Total Productive Maintenance
Varmeco Output Method
Total Quality Management
Business Process Re engineering
Yield Compass
=
Brovanta Consulting

The book size is 175 x 240 mm and will need a 10-15mm bleed. The spine is not known at this stage exactly and will need to be updated once the printing is finished but I suggest a 10mm until I have the exact size.

Our company colours are Pantone 288, R0,G75,B141, C100,M79,Y17,K3. Attached are some other publications that give a sense of what we like to portray, Some words which might add to this are: professional, elegance, quality, sleek.
Updates

Reason: After receiving the designs, I realised that I needed to update the brief with more and better quality information for designers to work with.

Target Market(s)

people in the accounting and insolvency industries, production managers and CEOs, Chief Operating Officers, members of the executive team of large companies and GMs of small companies.

Industry/Entity Type

Marketing

Requirements
Must have
• Communicate an image that shows an improvement or increase of something.
Very professional and elegant
Emphasis on the words 'Business Performance Improvement' in the title, subtitle also important
Must appeal to a high-end of the market audience
Nice to have
• Recommendation for your cover to be gloss or matt in print
Image can be indirectly related to money but not specifically
Somehow that it matches or is not so different to the attached brochure
Should not have
• Not be too loud or commercial
Book jacket. WIll be printed as soft cover first run and hard cover 2nd run

```html
<!DOCTYPE html>
<html lang="en">
<head>
<meta charset="utf-8">
<title>A Rounded Method for Enterprise Results Advancement – Book Jacket</title>
<link rel="stylesheet" href="https://fonts.googleapis.com/css2?family=Roboto+Condensed:wght@400;700;900&family=PT+Sans:wght@700&display=swap">
<style>
  :root {
    --brand-blue: #004b8d;
    --brand-blue-dark: #0b3f7c;
    --ink: #2b2b2b;
    --paper-top: #f4f4f4;
    --paper-bottom: #e4e5e6;
    --backdrop: #ececec;
    --white: #ffffff;
  }
  * { box-sizing: border-box; margin: 0; padding: 0; }
  html, body {
    width: 1200px; height: 800px; overflow: hidden;
    background: var(--backdrop);
  }
  .jacket {
    position: absolute; left: 147px; top: 98px;
    width: 906px; height: 604px;
    display: flex;
    box-shadow: 0 10px 30px rgba(0,0,0,0.12);
  }
  .cover {
    position: relative; width: 440px; height: 604px;
    background: linear-gradient(180deg, var(--paper-top), var(--paper-bottom));
    overflow: hidden;
  }
  .spine {
    position: relative; width: 26px; height: 604px;
    background: linear-gradient(90deg, #e2e3e4, #f1f1f1 50%, #e2e3e4);
    overflow: hidden;
  }
  .base-band {
    position: absolute; left: 0; right: 0; bottom: 0; height: 26px;
    background: var(--brand-blue);
  }

  /* Title block */
  .title-block { position: absolute; left: 0; right: 0; text-align: center; color: var(--brand-blue); font-family: "Roboto Condensed", sans-serif; }
  .title-kicker { display: block; font-weight: 700; color: var(--ink); font-size: 9px; letter-spacing: 0.5px; text-align: right; padding-right: 52px; }
  .title-line { display: block; font-weight: 900; line-height: 1; text-transform: uppercase; }
  .title-line--lead { font-size: 30px; letter-spacing: 0.2px; }
  .title-line--key { font-size: 56px; letter-spacing: 0.5px; margin-top: 2px; }
  .title-line--tail { font-size: 23px; letter-spacing: 0.3px; margin-top: 2px; }
  .title-rule { width: 344px; margin: 6px auto 5px; border-top: 2px dashed var(--ink); }
  .subtitle { font-family: "Roboto Condensed", sans-serif; font-weight: 700; color: var(--ink); font-size: 10.5px; letter-spacing: 1.6px; line-height: 1.35; text-transform: uppercase; }

  .front .title-block { top: 30px; }
  .back .title-block { top: 24px; }
  .back .title-line--lead { font-size: 25px; }
  .back .title-line--key { font-size: 46px; }
  .back .title-line--tail { font-size: 19px; }
  .back .title-rule { width: 282px; }
  .back .subtitle { font-size: 9px; letter-spacing: 1.2px; }

  /* Front artwork */
  .growth-chart { position: absolute; left: 0; top: 190px; width: 440px; height: 390px; }
  .climber-photo {
    position: absolute; left: 40px; top: 312px; width: 110px; height: 262px;
    background: linear-gradient(180deg, #d9d9d9 0%, #3a3a3c 18%, #1f1f22 100%);
    border-radius: 30px 30px 4px 4px;
  }
  .author-line {
    position: absolute; left: 0; right: 0; bottom: 0; height: 26px;
    font-family: "Roboto Condensed", sans-serif; font-weight: 700; font-size: 11px;
    letter-spacing: 1px; color: var(--white); text-align: center; line-height: 26px;
  }

  /* Spine */
  .spine-text {
    position: absolute; left: 50%; top: 14px;
    transform-origin: 0 0; transform: translateX(9px) rotate(90deg);
    white-space: nowrap; font-family: "Roboto Condensed", sans-serif; font-weight: 900;
    color: var(--brand-blue); font-size: 14px; letter-spacing: 0.6px; line-height: 18px;
  }
  .spine-author { color: var(--ink); font-size: 8px; font-weight: 700; margin-right: 8px; }

  /* Back copy */
  .scope-list {
    position: absolute; left: 0; right: 0; top: 200px; text-align: center;
    font-family: "PT Sans", sans-serif; font-weight: 700; color: var(--ink);
    font-size: 12.5px; line-height: 17px;
  }
  .scope-intro { margin: 0 auto 6px; width: 300px; }
  .scope-items { list-style: none; }
  .scope-result { font-size: 14px; margin-top: 3px; }

  .publisher-mark {
    position: absolute; left: 26px; bottom: 48px;
    display: flex; align-items: center; gap: 8px;
    font-family: "PT Sans", sans-serif; font-weight: 700; font-size: 17px;
    color: var(--brand-blue);
  }
  .publisher-square { width: 22px; height: 22px; background: var(--brand-blue); }
  .isbn-box {
    position: absolute; right: 24px; bottom: 40px; width: 122px; height: 62px;
    background: var(--brand-blue); color: var(--white);
    font-family: "PT Sans", sans-serif; font-weight: 700; font-size: 17px;
    display: flex; align-items: center; justify-content: center;
  }
</style>
</head>
<body>
<main class="jacket">

  <section class="cover back" aria-label="Back cover">
    <header class="title-block">
      <span class="title-kicker">GARETH POLWYN'S</span>
      <span class="title-line title-line--lead">A Rounded Method for</span>
      <span class="title-line title-line--key">Enterprise</span>
      <span class="title-line title-line--tail">Results Advancement</span>
      <div class="title-rule"></div>
      <p class="subtitle">Shape a Steady Refinement method<br>to fit your firm's character</p>
    </header>

    <div class="scope-list">
      <p class="scope-intro">Business Performance Improvement is also known as or can include:</p>
      <ul class="scope-items">
        <li>Continuous Improvement</li>
        <li>Process Improvement</li>
        <li>Lean Six Sigma</li>
        <li>Operational Excellence</li>
        <li>Total Productive Maintenance</li>
        <li>Varmeco Output Method</li>
        <li>Total Quality Management</li>
        <li>Business Process Reengineering</li>
        <li>Yield Compass</li>
        <li>=</li>
      </ul>
      <p class="scope-result">Brovanta Consulting</p>
    </div>

    <div class="publisher-mark">
      <span class="publisher-square"></span>
      <span>Brovanta Consulting</span>
    </div>
    <div class="isbn-box">ISBN</div>
    <div class="base-band"></div>
  </section>

  <section class="spine" aria-label="Spine">
    <p class="spine-text"><span class="spine-author">GARETH POLWYN'S</span>A ROUNDED METHOD FOR ENTERPRISE RESULTS ADVANCEMENT</p>
    <div class="base-band"></div>
  </section>

  <section class="cover front" aria-label="Front cover">
    <header class="title-block">
      <span class="title-line title-line--lead">A Rounded Method for</span>
      <span class="title-line title-line--key">Enterprise</span>
      <span class="title-line title-line--tail">Results Advancement</span>
      <div class="title-rule"></div>
      <p class="subtitle">Shape a Steady Refinement method<br>to fit your firm's character</p>
    </header>

    <svg class="growth-chart" viewBox="0 0 440 390" aria-hidden="true">
      <polyline fill="none" stroke="#151515" stroke-width="2.2" stroke-linejoin="round"
        points="14,384 60,380 96,376 118,370 132,356 150,366 162,340 176,345 190,328 200,322 214,312 222,292 236,298 250,276 262,262 270,268 282,244 296,236 304,214 318,212 330,190 344,178 350,186 360,164 372,170 380,144 386,124 392,116 404,122 418,58 426,36"/>
      <polygon points="426,24 420,42 432,42" fill="#151515"/>
    </svg>
    <div class="climber-photo" role="img" aria-label="Photo of a businessman in a dark suit stepping up the rising chart line"></div>

    <div class="base-band"></div>
    <p class="author-line">GARETH POLWYN B. MECH ENG., M. SC (KVT)</p>
  </section>

</main>
</body>
</html>
```